BOLD & MINIMALIST DESIGN NEEDED

We want a very bold but minimalistic business card design that is impactful and utilizes both sides of the business card. Our current logo is included for your use.

We want bold fonts and good use of negative space. We don't want the logo to overpower the design.

Target Market(s)

Professionals who are building new commercial buildings.

Industry/Entity Type

Construction

Contact Information for Business Card

Name, Title, email, office phone, cell phone, website

Font styles to use
Serif
Sans Serif

Requirements
Must have
• Bold design!

```html
<!DOCTYPE html>
<html lang="en">
<head>
<meta charset="utf-8">
<title>Ridgeway Design + Build — Stationery Set</title>
<link rel="stylesheet" href="https://fonts.googleapis.com/css2?family=Open+Sans:wght@400&family=Quicksand:wght@500;700&display=swap">
<style>
  :root {
    --board: #1d1d1d;
    --board-edge: #101010;
    --paper: #ffffff;
    --ink: #111111;
    --text: #4a4a4a;
    --muted: #777777;
    --rule: #8a8a8a;
    --green: #6cbf47;
    --ghost-grey: #d9d9d9;
    --ghost-green: #eef6e8;
    --label: #f2f2f2;
  }
  * { box-sizing: border-box; margin: 0; padding: 0; }
  html, body { width: 952px; height: 1200px; overflow: hidden; }
  body {
    position: relative;
    background: radial-gradient(ellipse at 50% 40%, #2a2a2a 0%, var(--board) 55%, var(--board-edge) 100%);
    font-family: "Quicksand", sans-serif;
    color: var(--text);
  }
  .sprite { position: absolute; width: 0; height: 0; }

  .label {
    position: absolute;
    font-family: "Open Sans", sans-serif;
    font-size: 17px;
    color: var(--label);
    line-height: 1;
  }
  .sheet { position: absolute; background: var(--paper); overflow: hidden; }

  .watermark {
    position: absolute;
    background: linear-gradient(120deg, var(--ghost-grey) 0%, var(--ghost-grey) 48%, var(--ghost-green) 52%, #f7faf5 100%);
    opacity: .9;
  }

  .brand {
    position: absolute;
    display: flex; flex-direction: column; align-items: center;
    gap: .35em;
  }
  .brand-mark { width: 1.6em; height: 1.6em; background: var(--green); }
  .brand-name {
    font-family: "Quicksand", sans-serif;
    font-weight: 700;
    color: var(--ink);
    text-transform: uppercase;
    text-align: center;
    line-height: 1.1;
    letter-spacing: .04em;
  }

  .contact { position: absolute; font-weight: 500; color: var(--text); line-height: 1.5; }
  .contact .row { display: flex; align-items: center; gap: .8em; }
  .contact ul { list-style: none; }
  .contact li { display: flex; align-items: center; gap: .35em; white-space: nowrap; }
  .contact svg { width: .95em; height: .95em; fill: none; stroke: var(--green); stroke-width: 2; }
  .contact .divider { width: 1px; align-self: stretch; background: var(--text); margin: .2em 0; }
  .contact .address { border-top: 1px solid var(--rule); margin-top: .2em; padding-top: .25em; white-space: nowrap; }

  /* Business card */
  .card { position: absolute; border-radius: 12px; overflow: hidden; }
  .card-front {
    left: 96px; top: 112px; width: 300px; height: 171px;
    background: radial-gradient(ellipse at 50% 30%, #2c2c2c 0%, #0b0b0b 80%);
  }
  .card-front .brand { left: 0; right: 0; top: 58px; font-size: 14px; }
  .card-front .brand-name { color: #2a2a2a; }
  .card-front .brand-mark { background: #3d6b2a; }
  .card-back {
    left: 156px; top: 300px; width: 300px; height: 171px;
    background: linear-gradient(135deg, #f1f1f1 0%, var(--paper) 60%);
  }
  .card-back .watermark { left: 30px; top: 36px; width: 160px; height: 135px; opacity: .6; }
  .card-back .brand { right: 18px; top: 14px; font-size: 9px; }
  .person { position: absolute; left: 16px; top: 92px; }
  .person-name { font-weight: 700; font-size: 11px; color: var(--ink); }
  .person-title { font-size: 8px; color: var(--text); }
  .card-back .contact { left: 16px; top: 122px; font-size: 7px; }

  /* Letterhead */
  .letterhead { left: 499px; top: 97px; width: 376px; height: 487px; }
  .letterhead .watermark { left: 60px; top: 202px; width: 316px; height: 285px; }
  .letterhead .brand { right: 14px; top: 14px; font-size: 11px; width: 100px; }
  .letterhead .contact { left: 13px; top: 438px; font-size: 7px; }

  /* Note pad */
  .notepad { left: 77px; top: 618px; width: 359px; height: 253px; }
  .notepad .watermark { left: 154px; top: 68px; width: 205px; height: 185px; }
  .notepad .brand { right: 14px; top: 14px; font-size: 8px; width: 72px; }
  .ruled { position: absolute; left: 13px; top: 72px; width: 334px; }
  .ruled span { display: block; height: 16.4px; border-top: 1px solid var(--rule); }
  .notepad .contact { left: 14px; top: 202px; font-size: 7px; }

  /* Compliment slip */
  .comp-slip { left: 492px; top: 690px; width: 384px; height: 181px; }
  .comp-slip .watermark { left: 215px; top: 30px; width: 169px; height: 151px; }
  .comp-slip .brand { left: 14px; top: 14px; font-size: 9px; width: 88px; }
  .comp-slip .contact { left: 14px; top: 133px; font-size: 7px; }
  .comp-note { position: absolute; left: 251px; top: 152px; font-size: 12px; font-weight: 500; color: var(--ink); }

  /* Envelope front */
  .env-front { left: 77px; top: 951px; width: 387px; height: 167px; }
  .env-front .watermark { left: 227px; top: 24px; width: 160px; height: 143px; }
  .env-front .brand { left: 13px; top: 88px; font-size: 9px; width: 84px; }
  .env-address {
    position: absolute; left: 13px; top: 145px; width: 126px;
    font-size: 7px; font-weight: 500; border-top: 1px solid var(--rule); padding-top: 3px; white-space: nowrap;
  }

  /* Envelope back */
  .env-back { left: 498px; top: 951px; width: 386px; height: 167px; }
  .env-back .flap { position: absolute; left: 0; top: 0; width: 386px; height: 70px; }
  .env-back .seal-ghost {
    position: absolute; left: 178px; top: 10px; width: 30px; height: 42px;
    background: linear-gradient(120deg, #bdbdbd 0%, #bdbdbd 50%, var(--ghost-green) 55%, #f3f8ef 100%);
  }
</style>
</head>
<body>

<svg class="sprite" aria-hidden="true">
  <symbol id="icon-mobile" viewBox="0 0 16 16"><rect x="4.5" y="1.5" width="7" height="13" rx="1"/></symbol>
  <symbol id="icon-phone" viewBox="0 0 16 16"><path d="M3 2.5l3 0 1.2 3-1.7 1.2a8 8 0 0 0 3.8 3.8l1.2-1.7 3 1.2v3a1.5 1.5 0 0 1-1.5 1.5A11 11 0 0 1 1.5 4 1.5 1.5 0 0 1 3 2.5z"/></symbol>
  <symbol id="icon-mail" viewBox="0 0 16 16"><rect x="1.5" y="3.5" width="13" height="9"/><path d="M1.5 3.5l6.5 5.5 6.5-5.5"/></symbol>
  <symbol id="icon-web" viewBox="0 0 16 16"><circle cx="8" cy="8" r="6.5"/><path d="M1.5 8h13M8 1.5c-3 3.5-3 9.5 0 13M8 1.5c3 3.5 3 9.5 0 13"/></symbol>
</svg>

<!-- Business card -->
<h2 class="label" style="left:77px;top:62px;">Business card_2</h2>
<section class="card card-front">
  <div class="brand"><span class="brand-mark"></span><span class="brand-name">Ridgeway<br>Design + Build</span></div>
</section>
<section class="card card-back">
  <div class="watermark" role="img" aria-label="Faint oversized brand symbol"></div>
  <div class="brand"><span class="brand-mark"></span><span class="brand-name">Ridgeway<br>Design + Build</span></div>
  <div class="person">
    <p class="person-name">Dana Whitfield</p>
    <p class="person-title">Founder</p>
  </div>
  <div class="contact">
    <div class="row">
      <ul><li><svg><use href="#icon-mobile"/></svg>3XX-2XX-9XXX</li><li><svg><use href="#icon-phone"/></svg>555-014-2200</li></ul>
      <span class="divider"></span>
      <ul><li><svg><use href="#icon-mail"/></svg>info@ridgeway-db.com</li><li><svg><use href="#icon-web"/></svg>www.ridgeway-db.com</li></ul>
    </div>
    <p class="address">1420 Cedar Hollow Rd. Lakemont, GA 30552</p>
  </div>
</section>

<!-- Letterhead -->
<h2 class="label" style="left:498px;top:62px;">Letterhead_2</h2>
<section class="sheet letterhead">
  <div class="watermark" role="img" aria-label="Faint oversized brand symbol"></div>
  <div class="brand"><span class="brand-mark"></span><span class="brand-name">Ridgeway<br>Design + Build</span></div>
  <div class="contact">
    <div class="row">
      <ul><li><svg><use href="#icon-mobile"/></svg>3XX-2XX-9XXX</li><li><svg><use href="#icon-phone"/></svg>555-014-2200</li></ul>
      <span class="divider"></span>
      <ul><li><svg><use href="#icon-mail"/></svg>info@ridgeway-db.com</li><li><svg><use href="#icon-web"/></svg>www.ridgeway-db.com</li></ul>
    </div>
    <p class="address">1420 Cedar Hollow Rd. Lakemont, GA 30552</p>
  </div>
</section>

<!-- Note pad -->
<h2 class="label" style="left:77px;top:585px;">Note Pads_2</h2>
<section class="sheet notepad">
  <div class="watermark" role="img" aria-label="Faint oversized brand symbol"></div>
  <div class="brand"><span class="brand-mark"></span><span class="brand-name">Ridgeway<br>Design + Build</span></div>
  <div class="ruled"><span></span><span></span><span></span><span></span><span></span><span></span><span></span><span></span></div>
  <div class="contact">
    <div class="row">
      <ul><li><svg><use href="#icon-mobile"/></svg>3XX-2XX-9XXX</li><li><svg><use href="#icon-phone"/></svg>555-014-2200</li></ul>
      <span class="divider"></span>
      <ul><li><svg><use href="#icon-mail"/></svg>info@ridgeway-db.com</li><li><svg><use href="#icon-web"/></svg>www.ridgeway-db.com</li></ul>
    </div>
    <p class="address">1420 Cedar Hollow Rd. Lakemont, GA 30552</p>
  </div>
</section>

<!-- Compliment slip -->
<h2 class="label" style="left:491px;top:655px;">Comp Slips_2</h2>
<section class="sheet comp-slip">
  <div class="watermark" role="img" aria-label="Faint oversized brand symbol"></div>
  <div class="brand"><span class="brand-mark"></span><span class="brand-name">Ridgeway<br>Design + Build</span></div>
  <div class="contact">
    <div class="row">
      <ul><li><svg><use href="#icon-mobile"/></svg>3XX-2XX-9XXX</li><li><svg><use href="#icon-phone"/></svg>555-014-2200</li></ul>
      <span class="divider"></span>
      <ul><li><svg><use href="#icon-mail"/></svg>info@ridgeway-db.com</li><li><svg><use href="#icon-web"/></svg>www.ridgeway-db.com</li></ul>
    </div>
    <p class="address">1420 Cedar Hollow Rd. Lakemont, GA 30552</p>
  </div>
  <p class="comp-note">With Compliments</p>
</section>

<!-- Envelope front -->
<h2 class="label" style="left:77px;top:915px;">ENV Front_2</h2>
<section class="sheet env-front">
  <div class="watermark" role="img" aria-label="Faint oversized brand symbol"></div>
  <div class="brand"><span class="brand-mark"></span><span class="brand-name">Ridgeway<br>Design + Build</span></div>
  <p class="env-address">1420 Cedar Hollow Rd. Lakemont, GA 30552</p>
</section>

<!-- Envelope back -->
<h2 class="label" style="left:498px;top:915px;">ENV Back_2</h2>
<section class="sheet env-back">
  <svg class="flap" viewBox="0 0 386 70" aria-hidden="true">
    <path d="M2 0 Q14 26 22 30 Q28 34 40 35 L180 60 Q193 63 206 60 L346 35 Q358 34 364 30 Q372 26 384 0"
          fill="none" stroke="#111" stroke-width="4.5" stroke-linejoin="round"/>
  </svg>
  <div class="seal-ghost" role="img" aria-label="Small faint brand symbol on the flap"></div>
</section>

</body>
</html>
```